Banner signature

Hi, looking for a banner for email signature 728 px wide and 200 px high
Could we have our 10 year logo and premium logo, a similar look and feel of our previous banner design (I've attached) and also include an aboriginal design with the Wording
This email comes to you from Gubbi Gubbi country
I've attached an example of some look and feels that we like.
Can we have the background of banner the Blue colour of our Fern & Pebble logo and

```html
<!DOCTYPE html>
<html lang="en">
<head>
<meta charset="utf-8">
<title>Email Signature Banner – Fern &amp; Pebble</title>
<link rel="stylesheet" href="https://fonts.googleapis.com/css2?family=Fredoka:wght@500;600&family=Permanent+Marker&display=block">
<style>
  :root {
    --stage: #232323;
    --sky-blue: #00aeef;
    --white: #ffffff;
    --sun-yellow: #fff200;
    --gold-light: #f6e08a;
    --gold-mid: #d9b23c;
    --gold-dark: #a57a17;
    --pattern-orange: #f58a2b;
    --pattern-rose: #c8607c;
    --pattern-navy: #3a55a8;
    --brand-ink: #1d3f8f;
  }
  * { margin: 0; padding: 0; box-sizing: border-box; }
  html, body {
    width: 1200px;
    height: 710px;
    overflow: hidden;
    background: var(--stage);
  }
  .banner {
    position: absolute;
    left: 50px;
    top: 228px;
    width: 1100px;
    height: 254px;
    background: var(--white);
    overflow: hidden;
  }
  .banner-shapes {
    position: absolute;
    inset: 0;
    width: 1100px;
    height: 254px;
  }
  .brand-mark {
    position: absolute;
    left: 38px;
    top: 10px;
    width: 148px;
    display: flex;
    flex-direction: column;
    align-items: center;
    gap: 6px;
  }
  .brand-seal {
    width: 118px;
    height: 118px;
    border-radius: 50%;
    background: radial-gradient(circle at 40% 35%, var(--gold-light), var(--gold-mid) 60%, var(--gold-dark));
  }
  .brand-name {
    font-family: "Fredoka", sans-serif;
    font-weight: 600;
    font-size: 17px;
    color: var(--brand-ink);
    white-space: nowrap;
  }
  .acknowledgement {
    position: absolute;
    left: 680px;
    top: 52px;
    width: 420px;
    text-align: center;
    color: var(--white);
  }
  .acknowledgement-intro {
    display: block;
    font-family: "Fredoka", sans-serif;
    font-weight: 500;
    font-size: 28px;
    line-height: 1.1;
  }
  .acknowledgement-country-name {
    display: block;
    font-family: "Permanent Marker", "Fredoka", sans-serif;
    font-size: 66px;
    line-height: 1.05;
    color: var(--sun-yellow);
    margin-top: 4px;
    white-space: nowrap;
  }
  .acknowledgement-country {
    display: block;
    font-family: "Fredoka", sans-serif;
    font-weight: 600;
    font-size: 54px;
    line-height: 1;
    margin-top: 0;
  }
</style>
</head>
<body>
  <div class="banner">
    <svg class="banner-shapes" viewBox="0 0 1100 254" xmlns="http://www.w3.org/2000/svg">
      <defs>
        <radialGradient id="artwork-tones" cx="0.5" cy="0.5" r="0.5">
          <stop offset="0.55" stop-color="var(--pattern-navy)"/>
          <stop offset="0.75" stop-color="var(--pattern-rose)"/>
          <stop offset="0.9" stop-color="var(--pattern-orange)"/>
          <stop offset="1" stop-color="var(--pattern-rose)"/>
        </radialGradient>
      </defs>
      <path d="M640 0 H1100 V254 H610 C650 190 665 90 640 0 Z" fill="var(--sky-blue)"/>
      <path d="M660 45 C820 10 960 2 1100 14 V30 C960 20 820 28 670 62 Z" fill="var(--white)"/>
      <path d="M0 200 C80 198 160 200 240 204 V216 C160 212 80 210 0 212 Z" fill="var(--sky-blue)"/>
      <path d="M0 226 C80 224 160 226 240 232 V244 C160 238 80 236 0 238 Z" fill="var(--sky-blue)"/>
      <g role="img" aria-label="Aboriginal dot-and-arc artwork surrounding the anniversary emblem">
        <circle cx="429" cy="127" r="222" fill="url(#artwork-tones)"/>
        <circle cx="429" cy="127" r="126" fill="var(--white)"/>
      </g>
      <g role="img" aria-label="10 year anniversary emblem">
        <circle cx="429" cy="127" r="108" fill="var(--gold-mid)"/>
        <circle cx="429" cy="127" r="96" fill="var(--gold-light)"/>
      </g>
    </svg>

    <div class="brand-mark">
      <div class="brand-seal"></div>
      <span class="brand-name">Fern &amp; Pebble</span>
    </div>

    <p class="acknowledgement">
      <span class="acknowledgement-intro">This email comes to you from</span>
      <span class="acknowledgement-country-name">Gubbi Gubbi</span>
      <span class="acknowledgement-country">COUNTRY</span>
    </p>
  </div>
</body>
</html>
```